KVR Inc Web Design

WHAT ARE WE DOING?
We are developing a new website look and feel for a new company called KVR Inc. This new look and feel should include colors, design elements, choice of photography and other imagery, fonts, and other user experience elements.

WHAT DO THEY DO?
KVR, Inc, makes tools for researchers who are studying protein-protein interactions. These molecules are the basic tools of biology, and serve as key targets for drug developers and disease researchers. The world of proteins is enormously complex, and companies like KVR provide researchers with critical tools that help them elucidate this world.

WHO ARE WE TALKING TO?
The target audience for this website are professional scientists working in university research or biopharma drug development. They are highly sophisticated consumers looking for key tools that will advance their research.

WHAT DO WE WANT THEM TO DO?
The site is an information resource for the customer exploring the tools that KVR sells and the scientific issues surrounding protein-protein interactions. They should be able to navigate easily to their content of choice, while the whole site should convey a professionalism that enhanced KVR’s credibility.

WHAT DOES THE KVR BRAND STAND FOR?
KVR stands for illumination. Proteins are challenging to study, and KVR exists to help shed light on their workings.

WHAT ARE THE KEY VALUES OF THE KVR BRAND?
Integrity. Innovation. Insight.

WHAT ARE THE EXECUTIONAL MANDITORIES?
The look and feel is completely up for grabs. Nothing is off the table.

WHAT ARE THE DELIVERABLES?
We need new designs for the following templates:
http://cms.marlowbench.com/
http://cms.marlowbench.com/products-and-services/instruments-3/bench-top-instruments/
http://cms.marlowbench.com/category/lab-study/

```html
<!DOCTYPE html>
<html lang="en">
<head>
<meta charset="utf-8">
<title>KVR Inc — Bench Top Instruments</title>
<link rel="stylesheet" href="https://fonts.googleapis.com/css2?family=Oswald:wght@300;400&family=Open+Sans:wght@400&family=Arimo:wght@400;700&display=swap">
<style>
:root{
  --orange:#f9b03c;
  --orange-link:#e8941a;
  --grey-dark:#666666;
  --grey-text:#6b6b6b;
  --grey-head:#444444;
  --grey-line:#a9a9a9;
  --grey-tab:#a3a3a3;
  --white:#ffffff;
  --footer:#676767;
}
*{box-sizing:border-box;margin:0;padding:0}
html,body{width:1030px;height:1200px;overflow:hidden;background:var(--white)}
body{position:relative;font-family:"Arimo",Arial,sans-serif;color:var(--grey-text)}
a{color:inherit;text-decoration:none}

/* header */
.site-header{position:absolute;left:0;top:0;width:1030px;height:104px}
.brand{position:absolute;left:45px;top:24px;font-family:"Oswald",sans-serif;font-weight:400;font-size:40px;line-height:1;color:var(--grey-dark)}
.utility-links{position:absolute;right:31px;top:25px;font-family:"Open Sans",sans-serif;font-size:10px;color:var(--grey-dark);letter-spacing:.3px}
.utility-links span{margin:0 6px}
.search{position:absolute;left:643px;top:47px;width:356px;height:30px;border:1px solid #9a9a9a;border-radius:5px;background:linear-gradient(#f7f7f7,#e6e6e6)}
.search-label{position:absolute;left:13px;top:4px;font-family:"Oswald",sans-serif;font-weight:300;font-size:15px;color:#555}
.search svg{position:absolute;right:9px;top:5px}

/* navigation */
.main-nav{position:absolute;left:0;top:104px;width:1030px;height:48px;background:var(--orange)}
.main-nav a{position:absolute;top:10px;font-family:"Oswald",sans-serif;font-weight:300;font-size:19px;color:var(--white)}

/* hero */
.page-hero{position:absolute;left:0;top:152px;width:1030px;height:154px;background:linear-gradient(180deg,#f2a93a 0%,#e6b979 30%,#c9c2b6 60%,#b8b8b8 100%)}
.page-hero h1{position:absolute;left:44px;top:28px;font-family:"Oswald",sans-serif;font-weight:400;font-size:54px;color:var(--white);letter-spacing:-.5px}
.page-hero svg{position:absolute;left:144px;bottom:0}

/* sidebar */
.side-nav{position:absolute;left:0;top:355px;width:169px;text-align:right;font-size:14.5px;color:#444}
.side-nav .overview{font-weight:700;line-height:16px;color:#333}
.side-nav .section{margin-top:34px;color:#555}
.side-nav .current{margin-top:7px;margin-right:-10px;color:#333}
.side-nav .current svg{margin-left:4px}
.side-nav .item{margin-top:7px;line-height:17px;color:#555}

/* content */
.content{position:absolute;left:245px;top:318px;width:750px}
.breadcrumb{font-family:"Open Sans",sans-serif;font-size:11px;color:#8a8a8a}
.content h2{font-weight:400;font-size:24px;color:var(--grey-head);margin-top:18px}
.intro{margin-top:22px;font-size:14.6px;line-height:21px}
.intro p+p{margin-top:21px}
.intro a{color:var(--orange-link)}
.photo{float:left;background:linear-gradient(135deg,#dde4ee 0%,#b7c4d6 50%,#8fa3bd 100%)}
.photo-lab{width:315px;height:210px;margin:0 30px 10px 0}

/* tabs */
.tabs{position:absolute;left:256px;top:716px;display:flex;gap:3px}
.tab{height:40px;padding:0 26px;border:1px solid var(--grey-line);border-bottom:none;border-radius:6px 6px 0 0;font-size:14.6px;line-height:39px;color:#555;background:var(--white)}
.tab.active{background:var(--grey-tab);color:var(--white);border-color:var(--grey-tab)}
.tab-panel{position:absolute;left:237px;top:756px;width:747px;height:308px;border:2px solid var(--grey-line);border-radius:12px;padding:24px 23px;font-size:14.6px;line-height:21px;color:#666}
.tab-panel p+p{margin-top:21px}
.photo-device{float:right;width:210px;height:141px;margin:0 0 10px 30px;background:linear-gradient(135deg,#eef1f4 0%,#c9d1da 60%,#9aa6b4 100%)}

/* footer */
.site-footer{position:absolute;left:0;top:1117px;width:1030px;height:83px;background:var(--footer);font-family:"Open Sans",sans-serif;font-size:13px;color:var(--white)}
.footer-links{position:absolute;left:30px;top:31px;display:flex;gap:14px}
.social{position:absolute;left:703px;top:22px;display:flex;gap:20px}
.social span{width:28px;height:28px;border-radius:50%;background:var(--white)}
.copyright{position:absolute;right:40px;top:31px}
</style>
</head>
<body>

<header class="site-header">
  <div class="brand">KVR Inc</div>
  <div class="utility-links"><a href="#">SITEMAP</a><span>|</span><a href="#">CONTACT US</a></div>
  <div class="search">
    <span class="search-label">ENTER KEYWORD</span>
    <svg width="22" height="20" viewBox="0 0 22 20" aria-hidden="true"><circle cx="8" cy="8" r="6" fill="none" stroke="#555" stroke-width="2"/><line x1="12.5" y1="12" x2="20" y2="18" stroke="#555" stroke-width="3" stroke-linecap="round"/></svg>
  </div>
</header>

<nav class="main-nav">
  <a href="#" style="left:47px">COMPANY</a>
  <a href="#" style="left:181px">PRODUCTS &amp; SERVICES</a>
  <a href="#" style="left:407px">LEARNING CENTER</a>
  <a href="#" style="left:597px">EVENTS</a>
  <a href="#" style="left:712px">KVR NEWS</a>
  <a href="#" style="left:846px">CONTACT US</a>
</nav>

<section class="page-hero">
  <h1>PRODUCTS &amp; SERVICES</h1>
  <svg width="34" height="20" viewBox="0 0 34 20" aria-hidden="true"><polygon points="0,20 17,3 34,20" fill="#fff"/></svg>
</section>

<aside class="side-nav">
  <div class="overview">PRODUCTS<br>OVERVIEW</div>
  <div class="section">INSTRUMENTS</div>
  <div class="current">Bench Top Instruments<svg width="6" height="10" viewBox="0 0 6 10" aria-hidden="true"><polygon points="0,0 6,5 0,10" fill="#333"/></svg></div>
  <div class="item">Microscope<br>Attachments</div>
</aside>

<main class="content">
  <div class="breadcrumb">Home » Products &amp; Services » Instruments » Bench Top Instruments</div>
  <h2>Bench Top Instruments</h2>
  <div class="intro">
    <div class="photo photo-lab" role="img" aria-label="Automated laboratory bench instrument with pipetting arm and sample plates"></div>
    <p>Maecenas imperdiet nisi eu justo dapibus, commodo <a href="#">venenatis massa tempus</a>. Morbi consectetur sed justo vitae dictum. Ut semper tincidunt accumsan.</p>
    <p>Nunc suscipit dui in massa ultricies, ac sagittis velit pulvinar. In scelerisque id lectus eu facilisis. <a href="#">Morbi et nunc non nulla</a> lobortis ultricies sit amet a turpis. Integer eget ullamcorper metus.</p>
    <p>Cras vitae nibh non dolor scelerisque porta.Nunc suscipit dui in massa ultricies, ac sagittis velit pulvinar. In scelerisque id lectus eu facilisis. <a href="#">Morbi et nunc non nulla</a> lobortis ultricies sit amet a turpis. Integer eget ullamcorper metus.</p>
  </div>
</main>

<div class="tabs">
  <div class="tab active">Overview</div>
  <div class="tab">Features</div>
  <div class="tab">Specifications</div>
  <div class="tab">FAQ’s</div>
  <div class="tab">Manuals</div>
</div>

<section class="tab-panel">
  <div class="photo-device" role="img" aria-label="Compact white bench top analysis instrument"></div>
  <p>Donec nec ipsum eget erat lacinia consectetur. Sed non turpis pretium, porttitor lorem eu, congue turpis. Vivamus viverra semper sem eget elementum. Aliquam augue libero, hendrerit a tortor vestibulum, rutrum suscipit ante. Curabitur a ligula ligula. In eget eros non metus elementum consequat id quis enim.</p>
  <p>Vivamus dignissim pharetra mi a tempor. Aenean pellentesque, arcu sed sodales vestibulum, nunc nulla molestie sem, ut imperdiet neque turpis sed purus. Nunc euismod tortor nec nibh venenatis convallis. Suspendisse magna augue, blandit et quam ac, fermentum dignissim purus. Curabitur tempor ac metus ut bibendum. Nulla id nisi semper, ornare nisi quis, laoreet dolor. Aliquam erat volutpat. Suspendisse ac metus sed orci mattis tempor ut eu lectus.</p>
</section>

<footer class="site-footer">
  <div class="footer-links">
    <a href="#">Home</a><a href="#">Company</a><a href="#">Products &amp; Services</a><a href="#">Contact Us</a><a href="#">Site Map</a><a href="#">Privacy Policy</a><a href="#">Terms</a>
  </div>
  <div class="social" aria-label="Social links"><span></span><span></span></div>
  <div class="copyright">© 2013 KVRINC</div>
</footer>

</body>
</html>
```